House flipping business web site needed

pinecrestholdingsgroup.example.
I am a residential developer in Northern NJ and I am looking for a fresh new updated website. I have an intro video about my company being made now. I don't update it very often but I want an easy format that I can add update photos to on projects I have worked on or homes I renovate for sale.

Target Market(s)

investors into my projects so a portfolio , people looking to sell their homes to me.

Industry/Entity Type

Real Estate Development

Number of Pages Required

4 page

Font styles to use
Serif

Colors
33b8a4
39a9d7
cadf82

Requirements
Must have
• space for an intro video about my company
• a portfolio with pictures and information about each project
• Markets we serve- Morris County, NJ
• My logo- already created
• SEO
• Yes I would like this to function over all platforms. Phone, computer, all platforms.
• history and background page
• I am looking for a completed page that I can upload to the site that hosts my website
Nice to have
• I want something creative, easy to navigate. modern.

```html
<!DOCTYPE html>
<html lang="en">
<head>
<meta charset="utf-8">
<title>Pinecrest Holdings</title>
<link href="https://fonts.googleapis.com/css2?family=Roboto:wght@300;400;500;700&family=Dancing+Script:wght@500&family=Lato:wght@400;700&display=swap" rel="stylesheet">
<style>
:root{
  --teal:#33b8a4;
  --teal-dark:#2a9f8d;
  --blue:#39a9d7;
  --blue-dark:#1f8cc0;
  --lime:#cadf82;
  --ink:#1b1b1b;
  --grey:#666;
  --light:#f4f4f4;
}
*{margin:0;padding:0;box-sizing:border-box}
html,body{width:1200px;height:2683px;overflow:hidden}
body{font-family:"Roboto",Arial,sans-serif;color:var(--ink);background:#fff;position:relative}
.abs{position:absolute}
.script{font-family:"Dancing Script",cursive;font-weight:500}
/* top bar */
.topbar{top:0;left:0;width:1200px;height:79px;background:#f6f6f6}
.contact-item{top:26px;display:flex;align-items:center;gap:14px;font-size:15px;font-weight:500}
.contact-item .ico{width:22px;height:22px;border-radius:4px;background:var(--teal);display:flex;align-items:center;justify-content:center}
.contact-item .ico.lime{background:var(--lime)}
.socials{top:26px;right:98px;display:flex;gap:9px}
.socials span{width:24px;height:24px;border:1.5px solid var(--teal);border-radius:50%}
/* nav */
.nav{top:79px;left:0;width:1200px;height:51px;background:linear-gradient(#45b5e3,#2a93c8);z-index:2}
.nav a{position:absolute;top:0;height:51px;line-height:51px;color:#fff;font-size:13px;text-decoration:none;text-transform:uppercase}
.nav a.active{background:#1f83ba;padding:0 24px}
.brand{top:0;left:510px;width:178px;height:157px;background:#fff;border-radius:0 0 30px 30px;box-shadow:0 3px 8px rgba(0,0,0,.2);display:flex;flex-direction:column;align-items:center;justify-content:center;gap:10px;z-index:10}
.brand .dot{width:56px;height:56px;border-radius:50%;background:var(--blue)}
.brand .name{font-family:"Lato",sans-serif;font-weight:700;font-size:19px;color:var(--blue-dark);letter-spacing:1px;text-align:center;line-height:1.1}
/* hero */
.hero{top:130px;left:0;width:1200px;height:521px;background:linear-gradient(160deg,#52683a 0%,#3c5328 40%,#6f7a5c 60%,#2f4020 100%)}
.hero-tag{left:97px;color:#fff;font-size:25px}
.hero-title{left:97px;color:#fff;font-size:40px;font-weight:500;letter-spacing:.5px}
.hero-text{left:97px;color:#fff;font-size:16px;line-height:30px;width:520px}
.btn{display:inline-block;color:#fff;font-size:14px;text-align:center;border-radius:3px}
.hero-btn{left:98px;width:140px;height:46px;line-height:44px;background:var(--teal);border:1px solid #fff;font-size:16px}
/* section headings */
.kicker{width:1200px;left:0;text-align:center;font-size:21px}
.heading{width:1200px;left:0;text-align:center;font-size:29px;font-weight:500;text-transform:uppercase}
/* about */
.video{top:808px;left:107px;width:504px;height:304px;border:6px solid #fff;box-shadow:0 0 6px rgba(0,0,0,.35);background:linear-gradient(135deg,#2f3a22,#5a5d40 50%,#3a2a22)}
.play{top:132px;left:214px;width:62px;height:42px;background:#d82727;border-radius:10px}
.about-lead{top:800px;left:656px;width:436px;font-size:16px;line-height:26px;color:var(--blue)}
.about-body{left:656px;width:436px;font-size:12px;line-height:22px;color:var(--grey)}
.about-btn{top:1062px;height:40px;line-height:40px;width:116px;font-size:12px}
/* markets */
.markets{top:1175px;left:0;width:1200px;height:406px;background:linear-gradient(#2fb39e,#34b9a4)}
.market{top:1316px;width:210px;text-align:center;color:#fff}
.market .ring{width:122px;height:122px;border-radius:50%;border:3px solid #fff;background:#54c5b2;margin:0 auto;display:flex;align-items:center;justify-content:center}
.market h3{font-size:16px;font-weight:500;margin-top:22px;white-space:nowrap}
.market p{font-size:12px;line-height:20px;margin:10px auto 0;width:178px}
/* projects */
.projects{top:1581px;left:0;width:1200px;height:425px;background:#f1f1ec}
.project{top:1720px;width:235px}
.project .photo{height:147px;border:3px solid #fff;box-shadow:0 0 3px rgba(0,0,0,.25)}
.project h4{font-size:16px;font-weight:500;margin-top:30px}
.project p{font-size:11px;line-height:20px;color:var(--teal);margin-top:8px;width:210px}
/* testimonials */
.testi{top:2163px;width:450px}
.testi .face{position:absolute;left:0;top:0;width:126px;height:111px;border:3px solid #fff;box-shadow:0 0 4px rgba(0,0,0,.3)}
.testi .who{position:absolute;left:149px;top:6px;font-size:15px;font-weight:500}
.testi .role{position:absolute;left:149px;top:29px;font-size:11px;color:#999}
.testi .stars{color:#f0a830;margin-left:14px;letter-spacing:1px}
.testi .quote{position:absolute;left:379px;top:0;font-size:60px;color:#ddd;font-family:Georgia,serif;line-height:1}
.testi .say{position:absolute;left:149px;top:59px;width:315px;font-size:12px;line-height:23px;color:#555;text-align:justify}
/* footer */
.footer{top:2337px;left:0;width:1200px;height:284px;background:linear-gradient(#3aa6d8,#2f96cc)}
.foot-col{top:2402px;color:#fff;font-size:13px}
.foot-col h5{font-size:16px;font-weight:500;text-transform:uppercase;margin-bottom:18px}
.foot-col li{list-style:none;line-height:30px}
.support{top:2402px;left:98px;width:404px;text-align:center;color:#fff}
.support h5{font-size:16px;font-weight:500;text-transform:uppercase}
.support .phone{font-family:"Lato",sans-serif;font-size:42px;margin-top:14px}
.support p{font-size:13px;line-height:24px;margin-top:10px}
.bottombar{top:2621px;left:0;width:1200px;height:62px;background:#1c7cb0;color:#fff;font-size:13px;text-align:center;line-height:62px}
</style>
</head>
<body>

<div class="abs topbar"></div>
<div class="abs contact-item" style="left:98px"><span class="ico"><svg width="12" height="12" viewBox="0 0 24 24"><path d="M6.6 10.8a15 15 0 0 0 6.6 6.6l2.2-2.2a1 1 0 0 1 1-.25 11 11 0 0 0 3.6.6 1 1 0 0 1 1 1V20a1 1 0 0 1-1 1A17 17 0 0 1 3 4a1 1 0 0 1 1-1h3.5a1 1 0 0 1 1 1 11 11 0 0 0 .6 3.6 1 1 0 0 1-.25 1z" fill="#fff"/></svg></span>+1 973-555-0148</div>
<div class="abs contact-item" style="left:289px"><span class="ico lime"><svg width="13" height="10" viewBox="0 0 26 20"><rect x="1" y="1" width="24" height="18" fill="none" stroke="#fff" stroke-width="2"/><path d="M1 1l12 10L25 1" fill="none" stroke="#fff" stroke-width="2"/></svg></span>@pinecrestholdings</div>
<div class="abs socials"><span></span><span></span><span></span><span></span><span></span><span></span></div>

<nav class="abs nav">
  <a class="active" style="left:98px" href="#">Home</a>
  <a style="left:209px" href="#">About Us</a>
  <a style="left:321px" href="#">Services</a>
  <a style="left:432px" href="#">Blog</a>
  <a style="left:721px" href="#">Portfolio</a>
  <a style="left:843px" href="#">Testimonial</a>
  <a style="left:976px" href="#">Contact</a>
  <span style="position:absolute;left:1062px;top:17px;width:1px;height:16px;background:#fff"></span>
  <svg style="position:absolute;left:1082px;top:18px" width="14" height="14" viewBox="0 0 14 14"><circle cx="6" cy="6" r="4.5" fill="none" stroke="#fff" stroke-width="2"/><path d="M9.3 9.3L13 13" stroke="#fff" stroke-width="2"/></svg>
</nav>
<div class="abs brand"><span class="dot"></span><span class="name">PINECREST<br>HOLDINGS</span></div>

<section>
  <div class="abs hero" role="img" aria-label="Photo of a weathered white cottage with a green lawn surrounded by tall trees"></div>
  <svg class="abs" style="top:346px;left:30px" width="22" height="84" viewBox="0 0 22 84"><path d="M20 2L2 42l18 40" fill="none" stroke="#fff" stroke-width="2"/></svg>
  <svg class="abs" style="top:346px;left:1148px" width="22" height="84" viewBox="0 0 22 84"><path d="M2 2l18 40L2 82" fill="none" stroke="#fff" stroke-width="2"/></svg>
  <div class="abs hero-tag script" style="top:266px">Investing In Our Neighborhoods</div>
  <h1 class="abs hero-title" style="top:305px">PINECREST HOLDINGS</h1>
  <p class="abs hero-text" style="top:368px">We will help you get out of your unwanted home We bring excellence to the home buying and renovation business.</p>
  <a class="abs btn hero-btn" style="top:461px">Read More Info</a>
</section>

<section>
  <div class="abs kicker script" style="top:706px;color:var(--teal)">Welcome to Our Company</div>
  <h2 class="abs heading" style="top:736px">About Our Pinecrest Holdings</h2>
  <div class="abs video" role="img" aria-label="Intro video still of a wooded home with a large deck">
    <span class="abs play"><svg width="62" height="42" viewBox="0 0 62 42"><path d="M25 13v16l14-8z" fill="#fff"/></svg></span>
  </div>
  <p class="abs about-lead">It is a long established fact that a reader will be distracted by the readable content of a page when looking at its layout.</p>
  <p class="abs about-body" style="top:870px">Many desktop publishing packages and web page editors now use Lorem Ipsum as their default model text, and a search for 'lorem ipsum' will uncover many web sites still in their infancy. Various versions have evolved over the years, sometimes by accident, sometimes on purpose (injected humour and the like).</p>
  <p class="abs about-body" style="top:973px">Contrary to popular belief, Lorem Ipsum is not simply random text. It has roots in a piece of classical Latin literature from 45 BC, making it over 2000 years old.</p>
  <a class="abs btn about-btn" style="left:656px;background:var(--blue)">Read More</a>
  <a class="abs btn about-btn" style="left:786px;background:var(--lime)">Get In Touch</a>
</section>

<section>
  <div class="abs markets"></div>
  <h2 class="abs heading" style="top:1224px;color:#fff">Markets We Serve</h2>
  <div class="abs kicker" style="top:1266px;font-size:12px;font-style:italic;color:#d8f1ec">Investing In Our Neighborhoods</div>
  <div class="abs market" style="left:79px"><div class="ring"><svg width="48" height="44" viewBox="0 0 48 44"><path d="M4 22L24 4l20 18M10 18v22h28V18" fill="none" stroke="#fff" stroke-width="4"/></svg></div><h3>RENOVATE HOMES</h3><p>We are a team of experienced in home buyers renovators</p></div>
  <div class="abs market" style="left:287px"><div class="ring"><svg width="44" height="44" viewBox="0 0 44 44"><rect x="4" y="4" width="18" height="38" fill="#fff"/><rect x="24" y="16" width="16" height="26" fill="#fff"/></svg></div><h3>REDEVELOPMENT</h3><p>We are a team of experienced in home buyers renovators</p></div>
  <div class="abs market" style="left:494px"><div class="ring"><svg width="48" height="40" viewBox="0 0 48 40"><path d="M2 18L24 2l22 16H2z" fill="#fff"/><rect x="8" y="18" width="32" height="20" fill="#fff"/><rect x="20" y="26" width="8" height="12" fill="#54c5b2"/></svg></div><h3>NEWLY BUILT HOME</h3><p>We are a team of experienced in home buyers renovators</p></div>
  <div class="abs market" style="left:701px"><div class="ring"><svg width="52" height="40" viewBox="0 0 52 40"><circle cx="26" cy="10" r="7" fill="#fff"/><circle cx="11" cy="14" r="5" fill="#fff"/><circle cx="41" cy="14" r="5" fill="#fff"/><path d="M14 38a12 12 0 0 1 24 0zM2 36a9 9 0 0 1 14-8v8zM50 36a9 9 0 0 0-14-8v8z" fill="#fff"/></svg></div><h3>OPTIONAL MEMBERSHIP</h3><p>We are a team of experienced in home buyers renovators</p></div>
  <div class="abs market" style="left:909px"><div class="ring"><svg width="40" height="48" viewBox="0 0 40 48"><rect x="3" y="6" width="34" height="40" rx="2" fill="none" stroke="#fff" stroke-width="4"/><rect x="12" y="2" width="16" height="8" fill="#fff"/><path d="M10 22l4 4 7-7M10 34l4 4 7-7" fill="none" stroke="#fff" stroke-width="3"/></svg></div><h3>ORGANIZED CHAOS</h3><p>We are a team of experienced in home buyers renovators</p></div>
</section>

<section>
  <div class="abs projects"></div>
  <h2 class="abs" style="top:1632px;left:98px;font-size:29px;font-weight:500">RECENT PROJECTS</h2>
  <p class="abs" style="top:1671px;left:98px;font-size:13px;color:var(--grey)">We are a team of experienced home buyers and renovators</p>
  <div class="abs project" style="left:98px"><div class="photo" role="img" aria-label="Two-storey beige house among trees" style="background:linear-gradient(#9fb3c6,#c8bca3 55%,#5a6a3a)"></div><h4>ROCKAWAY, NJ</h4><p>Many upgrades to this home, Added a new full bath, family room, office</p></div>
  <div class="abs project" style="left:355px"><div class="photo" role="img" aria-label="Grey colonial house with a garage" style="background:linear-gradient(#a9c6df,#8f9598 55%,#4f6d35)"></div><h4>DENVILLE, NJ</h4><p>Many upgrades to this home, Added a new full bath, family room, office</p></div>
  <div class="abs project" style="left:612px"><div class="photo" role="img" aria-label="Small blue cottage on a lawn" style="background:linear-gradient(#6f8a4a,#7fa0a8 50%,#5c8a3a)"></div><h4>BOONTON, NJ</h4><p>Many upgrades to this home, Added a new full bath, family room, office</p></div>
  <div class="abs project" style="left:869px"><div class="photo" role="img" aria-label="Wooded home with a large deck" style="background:linear-gradient(#4e6a30,#6b5038 60%,#4a5a2a)"></div><h4>NEW JERSEY.</h4><p>Many upgrades to this home, Added a new full bath, family room, office</p></div>
</section>

<section>
  <h2 class="abs heading" style="top:2060px">Our Client Testimonial</h2>
  <div class="abs kicker" style="top:2101px;font-size:12px;font-style:italic;color:#999">What Our Client Says About us</div>
  <div class="abs testi" style="left:98px">
    <div class="face" role="img" aria-label="Portrait of a smiling client" style="background:linear-gradient(#8a6e55,#c9a488)"></div>
    <div class="who">MARA QUILL DAWSON</div>
    <div class="role">Customers <span class="stars">★★★★★</span></div>
    <div class="quote">"</div>
    <p class="say">Contrary to popular belief, Lorem Ipsum is not simply random text. It has roots in a piece of classical Latin literature from 45 BC, making it over 2000 years old.</p>
  </div>
  <div class="abs testi" style="left:637px">
    <div class="face" role="img" aria-label="Portrait of a smiling client" style="background:linear-gradient(#dfe4ea,#e8c79a)"></div>
    <div class="who">MARA QUILL DAWSON</div>
    <div class="role">Customers <span class="stars">★★★★★</span></div>
    <div class="quote">"</div>
    <p class="say">Contrary to popular belief, Lorem Ipsum is not simply random text. It has roots in a piece of classical Latin literature from 45 BC, making it over 2000 years old.</p>
  </div>
</section>

<footer>
  <div class="abs footer"></div>
  <div class="abs support">
    <h5>Support</h5>
    <div class="phone">+1 973-555-0148</div>
    <p>@pinecrestholdings<br>Service@pinecrestholdingsgroup.example</p>
  </div>
  <div class="abs foot-col" style="left:582px"><h5>Quick Link</h5><ul><li>Team</li><li>Reviews</li><li>Blog</li><li>Contact</li></ul></div>
  <div class="abs foot-col" style="left:766px"><h5>Information</h5><ul><li>Terms and Condition</li><li>Privacy policy</li><li>Site Map</li></ul></div>
  <div class="abs foot-col" style="left:972px"><h5>Company</h5><ul><li>Why us</li><li>Contact</li><li>Customers</li><li>Affiliates</li></ul></div>
  <div class="abs bottombar">Copyrights@2016Company Name, All rights Reseve</div>
</footer>

</body>
</html>
```